Harlow Denatl Laboratory nees a window design

We want to make a window cover 8 feet wide and 6 feet tall to advertise our dental lab with all the products we produce<br/>: Digital Cad/Cam<br/>: Implants<br/>: Dentures<br/>: Cast Partials <br/>: Orthodontic appliances<br/><br/> and it has to include a service we provide for a denturist on site by appointment only.<br/><br/>Please use the sample logo below our colours are white backround and blue letters

Font styles to use
Script

Colors
ffffff
0355a3

Requirements
Nice to have
• a picture of a teddy bear on a dental chair, or some dental work particularly bridge work since our moto is Building bridges since 1976
Should not have
• real people

```html
<!DOCTYPE html>
<html lang="en">
<head>
<meta charset="utf-8">
<title>Harlow Dental Laboratory – Window Cover</title>
<link href="https://fonts.googleapis.com/css2?family=Oswald:wght@400;500&display=swap" rel="stylesheet">
<style>
  :root {
    --blue: #1f88cb;
    --blue-text: #1a7fc4;
    --grey: #c2c2c2;
    --grey-text: #9a9a9a;
    --white: #ffffff;
    --backdrop: #c7e5fb;
    --photo-top: linear-gradient(135deg, #2a6fa8 0%, #5d8fb8 45%, #d9d4cf 100%);
    --photo-bottom: linear-gradient(160deg, #d8d8d8 0%, #b9c9d8 40%, #5f9fd3 75%, #e4e4e4 100%);
  }
  html, body {
    margin: 0;
    padding: 0;
    width: 833px;
    height: 1200px;
    overflow: hidden;
    background: var(--backdrop);
    font-family: "Oswald", "Arial Narrow", sans-serif;
  }
  .window-cover {
    position: absolute;
    left: 16px;
    top: 300px;
    width: 800px;
    height: 600px;
    background: var(--white);
    overflow: hidden;
  }
  .tile {
    position: absolute;
    box-sizing: border-box;
    display: flex;
    flex-direction: column;
    justify-content: center;
  }
  .tile--blue { background: var(--blue); color: var(--white); }
  .tile--grey { background: var(--grey); color: var(--blue-text); }
  .tile__label {
    font-weight: 500;
    text-transform: uppercase;
    line-height: 1.02;
    letter-spacing: 0.2px;
    transform: scaleY(1.08);
    transform-origin: left center;
  }
  .services-title { left: 12px; top: 111px; width: 225px; height: 106px; padding-left: 22px; }
  .services-title .tile__label { font-size: 38px; }
  .service { font-size: 24px; }
  .service .tile__label { font-size: 24px; }
  .service--cad { left: 12px; top: 222px; width: 110px; height: 106px; padding-left: 12px; }
  .service--implants { left: 127px; top: 222px; width: 110px; height: 106px; padding-left: 9px; }
  .service--dentures { left: 12px; top: 333px; width: 110px; height: 105px; padding-left: 10px; }
  .service--cast { left: 127px; top: 333px; width: 110px; height: 105px; padding-left: 10px; }
  .service--ortho { left: 241px; top: 333px; width: 222px; height: 105px; padding-left: 50px; }

  .web-address {
    position: absolute;
    left: 115px;
    top: 46px;
    font-size: 21px;
    font-weight: 500;
    color: var(--blue-text);
    transform: scaleY(1.1);
  }
  .brand {
    position: absolute;
    left: 270px;
    top: 160px;
    width: 300px;
    text-align: center;
    color: var(--blue-text);
    font-weight: 400;
    text-transform: uppercase;
  }
  .brand__name { font-size: 42px; line-height: 1; letter-spacing: 3px; }
  .brand__sub { font-size: 20px; line-height: 1.3; letter-spacing: 2px; }
  .phone {
    position: absolute;
    left: 310px;
    top: 254px;
    display: flex;
    align-items: center;
    gap: 10px;
    font-size: 36px;
    font-weight: 500;
    color: var(--blue-text);
  }
  .phone svg { width: 28px; height: 28px; }
  .denturist-note {
    position: absolute;
    left: 84px;
    top: 450px;
    font-size: 14px;
    line-height: 1.3;
    color: var(--grey-text);
    text-transform: uppercase;
  }
  .email {
    position: absolute;
    left: 118px;
    top: 520px;
    display: flex;
    align-items: center;
    gap: 12px;
    font-size: 21px;
    font-weight: 500;
    color: var(--blue-text);
  }
  .email svg { width: 22px; height: 16px; }
  .photo { position: absolute; }
  .photo--patient { left: 578px; top: 116px; width: 222px; height: 212px; background: var(--photo-top); }
  .photo--team { left: 468px; top: 333px; width: 332px; height: 267px; background: var(--photo-bottom); }
</style>
</head>
<body>
  <main class="window-cover">
    <div class="tile tile--grey" style="left:12px;top:44px;width:63px;height:63px;"></div>
    <div class="tile tile--blue" style="left:351px;top:0;width:112px;height:111px;"></div>
    <div class="tile tile--blue" style="left:510px;top:48px;width:63px;height:63px;"></div>
    <div class="tile tile--grey" style="left:578px;top:0;width:103px;height:111px;"></div>
    <div class="tile tile--blue" style="left:686px;top:0;width:114px;height:111px;"></div>

    <div class="web-address">WWW.HARLOWDENTAL.COM</div>

    <div class="tile tile--blue services-title"><span class="tile__label">Our Services</span></div>
    <div class="tile tile--blue service service--cad"><span class="tile__label">Digital<br>CAD/CAM</span></div>
    <div class="tile tile--grey service service--implants"><span class="tile__label">Implants</span></div>
    <div class="tile tile--grey service service--dentures"><span class="tile__label">Dentures</span></div>
    <div class="tile tile--blue service service--cast"><span class="tile__label">Cast<br>Partials</span></div>
    <div class="tile tile--blue service service--ortho"><span class="tile__label">Orthodontic<br>Appliances</span></div>

    <div class="brand">
      <div class="brand__name">Harlow</div>
      <div class="brand__sub">Dental Laboratory</div>
    </div>

    <div class="phone">
      <svg viewBox="0 0 24 24" aria-hidden="true"><path fill="currentColor" d="M6.6 10.8a15.2 15.2 0 0 0 6.6 6.6l2.2-2.2a1 1 0 0 1 1-.25 11.4 11.4 0 0 0 3.6.57 1 1 0 0 1 1 1V20a1 1 0 0 1-1 1A17 17 0 0 1 3 4a1 1 0 0 1 1-1h3.5a1 1 0 0 1 1 1c0 1.25.2 2.45.57 3.57a1 1 0 0 1-.25 1z"/></svg>
      <span>312-555-0148</span>
    </div>

    <div class="photo photo--patient" role="img" aria-label="Photo of a smiling child in a dental chair with a teddy bear"></div>
    <div class="photo photo--team" role="img" aria-label="Photo of a dental team with a young patient"></div>
    <div class="tile tile--blue" style="left:686px;top:333px;width:63px;height:63px;opacity:.85;"></div>
    <div class="tile tile--blue" style="left:686px;top:547px;width:114px;height:53px;"></div>

    <div class="tile tile--blue" style="left:12px;top:444px;width:63px;height:156px;"></div>
    <div class="tile tile--grey" style="left:400px;top:444px;width:63px;height:62px;"></div>
    <div class="tile tile--blue" style="left:400px;top:511px;width:63px;height:89px;"></div>

    <p class="denturist-note" style="margin:0;">We provide for a denturist<br>on site by appointment only.</p>

    <div class="email">
      <svg viewBox="0 0 22 16" aria-hidden="true"><rect width="22" height="16" rx="2" fill="currentColor"/><path d="M1.5 2 11 9l9.5-7" fill="none" stroke="#fff" stroke-width="1.6"/></svg>
      <span>INFO@HARLOWDENTAL.COM</span>
    </div>
  </main>
</body>
</html>
```